Business Card Design & Gift cards, Gift Cert, Donation Card

Retail Gift Store-in addition to Business Cards we'd like sequenced 2 sided Gift cards, Gift Certificate Cards, and Donation Cards.please see examples and email for clarificationlogos attached with examples-
Gift Card, Gift Certificate and Donation Card will all be same style just differant upper right title, with back side info as example.
business card, as example is single sided.
looking for additional ideas for layout

Industry/Entity Type

Business

Contact Information for Business Card

211 Newman St.East Tawas, MI 48730989.362.8730Office@BrewKrew.com

Requirements
Must have
• Blue as per example
• Logos provided
• like gradiant background

```html
<!DOCTYPE html>
<html lang="en">
<head>
<meta charset="UTF-8">
<title>Tillow Marsh – Business Card &amp; Gift Card</title>
<link href="https://fonts.googleapis.com/css2?family=Comic+Neue:wght@400;700&display=swap" rel="stylesheet">
<style>
  :root {
    --backdrop: #4d4d4d;
    --card: #ffffff;
    --ink: #111111;
    --ink-soft: #666666;
    --rule: #555555;
    --divider: #d0d0d0;
    --band: #151515;
    --band-edge: #bdbdbd;
    --accent-blue: #1f2fc4;
    --accent-sun: #f5d63a;
  }
  * { margin: 0; padding: 0; box-sizing: border-box; }
  html, body { width: 1105px; height: 1200px; overflow: hidden; }
  body {
    background: var(--backdrop);
    font-family: "Comic Neue", "Comic Sans MS", cursive;
    position: relative;
  }
  .card {
    position: absolute;
    left: 196px;
    width: 720px;
    height: 412px;
    background: var(--card);
    border-radius: 28px;
    overflow: hidden;
  }
  .card--front { top: 146px; }
  .card--back { top: 602px; }

  /* Front */
  .brand-name {
    position: absolute;
    left: 40px; top: 176px;
    width: 320px;
    text-align: center;
    font-size: 40px;
    font-weight: 400;
    letter-spacing: 1px;
    color: var(--ink);
  }
  .front-divider {
    position: absolute;
    left: 356px; top: 75px;
    width: 2px; height: 249px;
    background: var(--divider);
  }
  .contact {
    position: absolute;
    left: 394px;
    color: var(--ink-soft);
    font-size: 21px;
    line-height: 26px;
  }
  .contact--address { top: 83px; }
  .contact--reach { top: 145px; line-height: 27px; }
  .contact--products { top: 213px; }
  .contact-row { display: flex; align-items: center; gap: 8px; }
  .contact-row svg { width: 15px; height: 15px; fill: var(--ink); }
  .front-band-edge {
    position: absolute; left: 0; right: 0; top: 379px;
    height: 3px; background: var(--band-edge);
  }
  .front-band {
    position: absolute; left: 0; right: 0; top: 384px; bottom: 0;
    background: var(--band);
  }

  /* Back */
  .card-number {
    position: absolute; right: 34px; top: 33px;
    font-size: 18px; color: var(--ink);
  }
  .field-label {
    position: absolute;
    color: var(--ink);
    white-space: nowrap;
  }
  .field-label--large { font-size: 27px; }
  .field-label--small { font-size: 21px; }
  .field-line {
    position: absolute;
    height: 1.5px;
    background: var(--rule);
  }
  .mascot-art {
    position: absolute;
    left: 536px; top: 220px;
    width: 117px; height: 128px;
    border-radius: 10px;
    background: linear-gradient(160deg, var(--accent-blue) 0%, var(--accent-blue) 55%, var(--accent-sun) 100%);
  }
</style>
</head>
<body>
  <section class="card card--front" aria-label="Business card">
    <div class="brand-name">Tillow Marsh</div>
    <div class="front-divider"></div>
    <div class="contact contact--address">
      <div>482 Larkfield Ave.</div>
      <div>Cedar Bluff, MI 48614</div>
    </div>
    <div class="contact contact--reach">
      <div class="contact-row">
        <svg viewBox="0 0 24 24" aria-hidden="true"><path d="M6.6 10.8a15.1 15.1 0 0 0 6.6 6.6l2.2-2.2a1 1 0 0 1 1-.25 11.4 11.4 0 0 0 3.6.57 1 1 0 0 1 1 1V20a1 1 0 0 1-1 1A17 17 0 0 1 3 4a1 1 0 0 1 1-1h3.5a1 1 0 0 1 1 1c0 1.25.2 2.45.57 3.57a1 1 0 0 1-.25 1z"/></svg>
        <span>989.517.4296</span>
      </div>
      <div class="contact-row">
        <svg viewBox="0 0 24 24" aria-hidden="true"><path d="M2 5h20v14H2z M2 5l10 7 10-7" fill="var(--ink)"/><path d="M3 6l9 6.3L21 6" fill="none" stroke="#fff" stroke-width="1.6"/></svg>
        <span>Office@TillowMarsh.com</span>
      </div>
    </div>
    <div class="contact contact--products">
      <div>Gourmet Food</div>
      <div>Fine Wines | Gift Baskets</div>
      <div>Kitchen &amp; Bath Accessories</div>
      <div>Candles | Cards | Soaps</div>
    </div>
    <div class="front-band-edge"></div>
    <div class="front-band"></div>
  </section>

  <section class="card card--back" aria-label="Gift card back">
    <div class="card-number">Card Number : 58724</div>

    <div class="field-label field-label--large" style="left:58px; top:80px;">To :</div>
    <div class="field-line" style="left:119px; width:541px; top:105px;"></div>

    <div class="field-label field-label--large" style="left:58px; top:138px;">Form :</div>
    <div class="field-line" style="left:146px; width:514px; top:162px;"></div>

    <div class="field-label field-label--small" style="left:55px; top:225px;">Date&nbsp; Issued :</div>
    <div class="field-line" style="left:209px; width:306px; top:245px;"></div>

    <div class="field-label field-label--small" style="left:55px; top:273px;">Expiration Date :</div>
    <div class="field-line" style="left:239px; width:276px; top:293px;"></div>

    <div class="field-label field-label--small" style="left:55px; top:322px;">Employee :</div>
    <div class="field-line" style="left:189px; width:326px; top:341px;"></div>

    <div class="mascot-art" role="img" aria-label="Blue dancing figure stepping over a rising yellow sun"></div>
  </section>
</body>
</html>
```